Harbor Crestline (Business Card Design)

Need business cards designed. Something modern, chic, and sleek. Mabye the back of the card should be the navy blue that is in the logo and then just the logo on the back.

Target Market(s)

Those in the hotel, office, and renovation industry

Contact Information for Business Card

1. Logo 2. Dorian Fenwick 3. CEO/Founder 4. Phone: (833) HarbCre / (833) 427-2731 5. Email: dorian@theharborcrestline.com 6. Website: www.theharborcrestline.com

Font styles to use
Other font styles liked:
• Look at the logo font and base the font for everything else off of that.

Colors
0054AA
0677BA
7BADD7
CADEEF
E8F1F8

Requirements
Must have
• Colors that are associated in the logo
Nice to have
• Sleek modern clean and chic design.

```html
<!DOCTYPE html>
<html lang="en">
<head>
<meta charset="utf-8">
<title>Harbor Crestline – Business Card</title>
<link href="https://fonts.googleapis.com/css2?family=Open+Sans:wght@400;700&display=swap" rel="stylesheet">
<style>
  :root {
    --navy: #0f1a42;
    --gold: #cfa44a;
    --white: #ffffff;
    --backdrop: #2a2b2f;
  }
  * { box-sizing: border-box; margin: 0; padding: 0; }
  html, body { width: 1200px; height: 947px; overflow: hidden; }
  body {
    background: var(--backdrop);
    font-family: "Open Sans", sans-serif;
    display: flex;
    flex-direction: column;
    align-items: center;
    justify-content: center;
    gap: 44px;
  }
  .card {
    position: relative;
    width: 680px;
    height: 389px;
    border-radius: 26px;
    background: var(--navy);
    overflow: hidden;
  }
  /* Front */
  .card--front {
    display: flex;
    align-items: center;
    justify-content: center;
    gap: 18px;
  }
  .brand-mark {
    width: 22px;
    height: 22px;
    background: var(--gold);
  }
  .brand-name {
    color: var(--white);
    font-weight: 700;
    font-size: 42px;
    letter-spacing: 0.04em;
    text-transform: uppercase;
  }
  /* Back */
  .name-tab {
    position: absolute;
    top: 22px;
    right: 0;
    width: 36px;
    height: 58px;
    background: var(--gold);
  }
  .identity {
    position: absolute;
    top: 24px;
    right: 56px;
    text-align: right;
  }
  .identity__name {
    color: var(--gold);
    font-weight: 700;
    font-size: 30px;
    line-height: 1.15;
  }
  .identity__title {
    color: var(--white);
    font-size: 17px;
  }
  .contacts {
    position: absolute;
    left: 0;
    bottom: 34px;
    display: flex;
    flex-direction: column;
    gap: 8px;
    list-style: none;
  }
  .contact {
    display: flex;
    align-items: center;
    gap: 16px;
    color: var(--white);
    font-size: 18px;
  }
  .contact__tab {
    width: 72px;
    height: 36px;
    background: var(--gold);
    display: flex;
    align-items: center;
    justify-content: flex-end;
    padding-right: 12px;
  }
  .contact__tab svg { width: 16px; height: 16px; fill: var(--white); }
</style>
</head>
<body>
  <section class="card card--front" aria-label="Card front">
    <span class="brand-mark"></span>
    <h1 class="brand-name">Harbor Crestline</h1>
  </section>

  <section class="card card--back" aria-label="Card back">
    <span class="name-tab"></span>
    <div class="identity">
      <p class="identity__name">Dorian Fenwick</p>
      <p class="identity__title">Founder + CEO</p>
    </div>
    <ul class="contacts">
      <li class="contact">
        <span class="contact__tab"><svg viewBox="0 0 24 24"><path d="M6.6 10.8a15.1 15.1 0 0 0 6.6 6.6l2.2-2.2a1 1 0 0 1 1-.25 11.4 11.4 0 0 0 3.6.57 1 1 0 0 1 1 1V20a1 1 0 0 1-1 1A17 17 0 0 1 3 4a1 1 0 0 1 1-1h3.5a1 1 0 0 1 1 1c0 1.25.2 2.45.57 3.57a1 1 0 0 1-.25 1z"/></svg></span>
        (833) 427-2731
      </li>
      <li class="contact">
        <span class="contact__tab"><svg viewBox="0 0 24 24"><path d="M2 5h20v14H2z M2 5l10 8 10-8" stroke="#cfa44a" stroke-width="1.5"/></svg></span>
        dorian@theharborcrestline.com
      </li>
      <li class="contact">
        <span class="contact__tab"><svg viewBox="0 0 24 24"><circle cx="12" cy="12" r="10"/><path d="M2 12h20M12 2c3 3 3 17 0 20M12 2c-3 3-3 17 0 20" stroke="#cfa44a" stroke-width="1.4" fill="none"/></svg></span>
        www.theharborcrestline.com
      </li>
    </ul>
  </section>
</body>
</html>
```